Business Card Design for Property Development Company Director

I am looking for a professional and unforgettable business card design for our Director of our Property Development Company.
Please see attached .pptx file to find out what information to include. You don't have to follow the exact format shown in the file - I am interested to see your creative flair using the information provided.

```html
<!DOCTYPE html>
<html lang="en">
<head>
<meta charset="utf-8">
<title>Kestrel Property Group – Business Card</title>
<link href="https://fonts.googleapis.com/css2?family=Arimo:wght@400;700&display=swap" rel="stylesheet">
<style>
  :root {
    --brand-blue: #0f57a8;
    --brand-grey: #5f5f61;
    --text-grey: #6a6a6c;
    --card-white: #ffffff;
    --backdrop: #1e1e21;
  }
  html, body {
    margin: 0;
    padding: 0;
    width: 1200px;
    height: 800px;
    overflow: hidden;
    background: var(--backdrop);
    font-family: "Arimo", Arial, sans-serif;
  }
  .stage {
    width: 1200px;
    height: 800px;
    display: flex;
    align-items: center;
    justify-content: center;
    gap: 40px;
  }
  .card {
    position: relative;
    width: 525px;
    height: 300px;
    background: var(--card-white);
    overflow: hidden;
    box-shadow: 0 18px 40px rgba(0,0,0,0.55);
  }

  /* Reverse side */
  .card-reverse {
    display: flex;
    flex-direction: column;
    align-items: center;
    justify-content: center;
    text-align: center;
  }
  .tagline {
    margin: 0 0 28px;
    color: var(--text-grey);
    font-weight: 700;
    font-size: 17px;
    line-height: 1.3;
    letter-spacing: 0.5px;
  }
  .brand {
    display: flex;
    align-items: center;
    gap: 12px;
    margin-bottom: 34px;
  }
  .brand-square {
    width: 34px;
    height: 34px;
    background: var(--brand-blue);
  }
  .brand-name {
    color: var(--brand-blue);
    font-weight: 700;
    font-size: 30px;
    line-height: 1;
    text-align: left;
  }
  .brand-name small {
    display: block;
    font-size: 13px;
    letter-spacing: 2.5px;
    margin-top: 3px;
  }
  .invite {
    margin: 0;
    color: var(--text-grey);
    font-size: 11px;
  }
  .invite strong { font-weight: 700; }

  /* Front side */
  .card-front .front-shape {
    position: absolute;
    inset: 0;
    width: 100%;
    height: 100%;
  }
  .front-details {
    position: absolute;
    top: 30px;
    left: 268px;
    right: 20px;
    color: var(--card-white);
  }
  .front-brand {
    font-weight: 700;
    font-size: 26px;
    line-height: 1;
    margin: 0 0 20px;
  }
  .front-brand span {
    display: block;
    font-size: 12px;
    font-weight: 700;
    letter-spacing: 2.5px;
    margin-top: 3px;
  }
  .person-name {
    margin: 0;
    font-weight: 700;
    font-size: 16px;
  }
  .person-role {
    margin: 0 0 10px;
    font-size: 12px;
  }
  .contact-list {
    list-style: none;
    margin: 0;
    padding: 0;
    font-size: 11px;
    line-height: 1.65;
  }
  .contact-list li {
    display: flex;
    align-items: center;
    gap: 7px;
    white-space: nowrap;
  }
  .contact-list svg {
    width: 10px;
    height: 10px;
    fill: var(--card-white);
    flex: none;
  }
  .contact-list .licence { padding-left: 17px; }
</style>
</head>
<body>
<main class="stage">

  <section class="card card-reverse" aria-label="Business card reverse">
    <p class="tagline">PROPERTY DEVELOPMENT<br>&amp; SITE ACQUISITION SPECIALISTS</p>
    <div class="brand">
      <span class="brand-square" aria-hidden="true"></span>
      <span class="brand-name">KESTREL<small>PROPERTY GROUP</small></span>
    </div>
    <p class="invite">Ask me about our <strong>INVESTMENT &amp; PARTNERSHIP</strong> opportunities</p>
  </section>

  <section class="card card-front" aria-label="Business card front">
    <svg class="front-shape" viewBox="0 0 525 300" preserveAspectRatio="none" aria-hidden="true">
      <path d="M120 0 H525 V300 H450 Q380 262 270 240 Q205 225 188 175 Q168 60 120 0 Z" fill="var(--brand-blue)"/>
      <path d="M120 0 Q168 60 188 175 Q205 225 270 240 Q380 262 450 300" fill="none" stroke="var(--card-white)" stroke-width="6"/>
    </svg>
    <div class="front-details">
      <p class="front-brand">KESTREL<span>PROPERTY GROUP</span></p>
      <p class="person-name">DANIEL MERCER</p>
      <p class="person-role">Director</p>
      <ul class="contact-list">
        <li><svg viewBox="0 0 10 10"><path d="M2 0.5 L3.6 2.6 L2.7 3.6 Q3.6 5.6 5.9 7 L7 6.1 L9.5 7.6 L8.4 9.5 Q3 9 0.5 2 Z"/></svg>0400 123 456</li>
        <li><svg viewBox="0 0 10 10"><path d="M0 2 H10 V8 H0 Z M0.8 2.6 L5 5.6 L9.2 2.6" stroke="#0f57a8" stroke-width="0.8"/></svg>daniel@kestrelgroup.com.au</li>
        <li><svg viewBox="0 0 10 10"><circle cx="5" cy="5" r="4.6"/></svg>www.kestrelgroup.com.au</li>
        <li class="licence">Real Estate Lic: 1234567 &amp; 1234568</li>
      </ul>
    </div>
  </section>

</main>
</body>
</html>
```